Business Intelligence / Data Visualization Firm Seeking World Class Power Point Deck

Vela Crest delivers enterprise business intelligence and data visualization solutions enabling clients to see their business as they've never seen it - we transform complex, unstructured data into simple insight that facilitates intelligent decision making, revenue growth and risk reduction. We're seeking a world class power point template for internal, client and conference presentations.

Please visit velacrest.example for more company context.
*Note: A website photo has been uploaded and may be used or not used - designer discretion.

Additional context:
We use Lumadrift: https://lumadrift.norvex.example/products/predictive-analytics.

Target Market(s)

CXOs at Meridian 100 companies | small and medium business owners (BI / data-viz experts and also decision makers who don't actually understand BI / data-viz).

Industry/Entity Type

Professional Service

Font styles to use
Sans Serif
Other font styles liked:
• Our logo is Expansiva (uploaded), our site is Tahoma. Please use your discretion,.

Colors
ec1f27
ffffff
000000

Requirements
Must have
• PPT format, editable.
• Prefer simple, clean, strong presentation.
Nice to have
• Designs that relate to data, analytics, solutions, automation and transforming complexity into simplicity.
• Reusable icons.

```html
<!DOCTYPE html>
<html lang="en">
<head>
<meta charset="utf-8">
<title>Vela Crest – Individual Slides</title>
<link href="https://fonts.googleapis.com/css2?family=Alegreya:wght@800&family=Michroma&family=Open+Sans:wght@400;600;700&display=swap" rel="stylesheet">
<style>
:root{
  --red:#ec1f27;
  --black:#000000;
  --white:#ffffff;
  --ink:#3a3a3a;
  --muted:#8a8a8a;
  --rule:#d9d9d9;
  --slide-bg:#f6f6f6;
  --wood-a:#9a8666;
  --wood-b:#7f6c50;
  --heading-grey:#6a6a6a;
}
*{box-sizing:border-box;margin:0;padding:0}
html,body{width:1200px;height:1200px;overflow:hidden;background:var(--white)}
body{position:relative;font-family:"Open Sans",Arial,sans-serif}
.page-title{position:absolute;top:10px;left:0;width:1200px;text-align:center;font-family:"Alegreya",Georgia,serif;font-weight:800;font-size:25px;color:var(--heading-grey);letter-spacing:.3px}
.board{position:absolute;left:86px;top:64px;width:1050px;height:1136px;background:linear-gradient(135deg,var(--wood-a),var(--wood-b) 55%,var(--wood-a))}
.slide{position:absolute;width:281px;height:158px;background:var(--slide-bg);box-shadow:0 3px 6px rgba(0,0,0,.45);overflow:hidden}
.slide svg.content{position:absolute;inset:0;width:281px;height:158px}
.slide-title{position:absolute;left:8px;top:6px;font-family:"Michroma",Arial,sans-serif;font-weight:400;font-size:7.2px;color:var(--black);letter-spacing:.4px;white-space:nowrap}
.slide-title::before{content:"";position:absolute;left:-8px;top:-2px;width:3px;height:11px;background:var(--red)}
.slide-sub{position:absolute;left:8px;top:17px;font-size:2.6px;color:var(--muted)}
.brand-mark{position:absolute;right:5px;top:4px;width:58px;height:11px;background:var(--black);color:var(--white);font-family:"Michroma",Arial,sans-serif;font-size:5.4px;line-height:11px;text-align:center;letter-spacing:.5px}
.slide-footer{position:absolute;left:0;bottom:0;width:281px;height:6px;background:var(--black);color:var(--white);font-size:2.6px;line-height:6px;padding-left:8px;letter-spacing:.6px}
.slide-footer::after{content:"";position:absolute;left:0;top:0;width:4px;height:6px;background:var(--red)}
.copy{font-family:"Open Sans",Arial,sans-serif;font-size:3px;fill:var(--muted)}
.label{font-family:"Open Sans",Arial,sans-serif;font-size:3.4px;fill:var(--ink)}
.label-b{font-family:"Open Sans",Arial,sans-serif;font-size:4px;font-weight:700;fill:var(--ink)}
.on-dark{font-family:"Open Sans",Arial,sans-serif;font-size:3.4px;font-weight:700;fill:var(--white)}
.big{font-family:"Open Sans",Arial,sans-serif;font-weight:700;fill:var(--white)}
.r{fill:var(--red)}.k{fill:var(--black)}.g{fill:#dedede}.gd{fill:#555}.gk{fill:#333}
.photo-a{fill:url(#photoCool)}.photo-b{fill:url(#photoWarm)}
.photo-panel{position:absolute}
</style>
</head>
<body>
<h1 class="page-title">01 c - Individual Slides</h1>
<div class="board"></div>

<svg width="0" height="0" style="position:absolute">
  <defs>
    <linearGradient id="photoCool" x1="0" y1="0" x2="1" y2="1"><stop offset="0" stop-color="#4a4e57"/><stop offset="1" stop-color="#b9bec6"/></linearGradient>
    <linearGradient id="photoWarm" x1="0" y1="0" x2="1" y2="1"><stop offset="0" stop-color="#c9ced8"/><stop offset="1" stop-color="#7b8393"/></linearGradient>
    <polygon id="hex" points="0,-14 12.1,-7 12.1,7 0,14 -12.1,7 -12.1,-7"/>
  </defs>
</svg>

<!-- Row 1 -->
<section class="slide" style="left:147px;top:93px">
  <svg class="content" viewBox="0 0 281 158">
    <text class="copy" x="18" y="32">Vela Crest turns complex data into simple insight for faster and smarter decisions every day,</text>
    <text class="copy" x="18" y="37">helping leaders grow revenue, reduce risk and see the whole business clearly.</text>
    <g>
      <polygon class="gd" points="40,130 52,90 52,134"/><polygon class="gk" points="52,90 64,130 52,134"/>
      <polygon class="gd" points="80,130 92,100 92,134"/><polygon class="gk" points="92,100 104,130 92,134"/>
      <polygon class="gd" points="120,130 132,92 132,134"/><polygon class="gk" points="132,92 144,130 132,134"/>
      <polygon class="gd" points="160,130 172,82 172,134"/><polygon class="gk" points="172,82 184,130 172,134"/>
      <polygon class="gd" points="200,130 212,78 212,134"/><polygon class="gk" points="212,78 224,130 212,134"/>
      <polygon class="gd" points="240,130 252,68 252,134"/><polygon class="gk" points="252,68 264,130 252,134"/>
    </g>
    <circle class="r" cx="50" cy="72" r="6"/><text class="on-dark" x="46.5" y="73.2">50%</text>
    <circle class="k" cx="87" cy="90" r="6"/><text class="on-dark" x="83.5" y="91.2">20%</text>
    <text class="label-b" x="123" y="70">SERIES</text>
    <circle class="r" cx="122" cy="79" r="5"/><text class="on-dark" x="119" y="80.2">38%</text>
    <circle class="k" cx="158" cy="70" r="5"/><text class="on-dark" x="155" y="71.2">50%</text>
    <circle class="r" cx="196" cy="63" r="6"/><text class="on-dark" x="192.5" y="64.2">52%</text>
    <circle class="k" cx="232" cy="54" r="6"/><text class="on-dark" x="228.5" y="55.2">80%</text>
    <g class="label"><text x="43" y="143">2012</text><text x="83" y="143">2013</text><text x="123" y="143">2014</text><text x="163" y="143">2015</text><text x="203" y="143">2016</text><text x="243" y="143">2017</text></g>
  </svg>
  <h2 class="slide-title">CHART STYLE - 2</h2><p class="slide-sub">Enter your subtitle here</p>
  <div class="brand-mark">VELA CREST</div><div class="slide-footer">WWW.VELACREST.EXAMPLE</div>
</section>

<section class="slide" style="left:475px;top:93px">
  <svg class="content" viewBox="0 0 281 158">
    <text style="font:700 11px 'Open Sans',sans-serif;fill:var(--red)" x="70" y="59">86%</text>
    <text class="copy" x="105" y="45">Vela Crest has turned raw records into clear</text>
    <text class="copy" x="105" y="51">insight since day one, helping every team decide</text>
    <text class="copy" x="105" y="57">with confidence and act on it fast.</text>
    <g>
      <path class="k" d="M26,125 C34,125 36,117 42,117 C48,117 50,125 58,125Z"/>
      <path class="r" d="M48,125 C56,125 58,112 64,112 C70,112 72,125 80,125Z"/>
      <path class="k" d="M70,125 C78,125 80,108 86,108 C92,108 94,125 102,125Z"/>
      <path class="r" d="M92,125 C100,125 102,103 108,103 C114,103 116,125 124,125Z"/>
      <path class="k" d="M114,125 C122,125 124,98 130,98 C136,98 138,125 146,125Z"/>
      <path class="r" d="M136,125 C144,125 146,93 152,93 C158,93 160,125 168,125Z"/>
      <path class="k" d="M158,125 C166,125 168,88 174,88 C180,88 182,125 190,125Z"/>
      <path class="r" d="M180,125 C188,125 190,84 196,84 C202,84 204,125 212,125Z"/>
      <path class="k" d="M202,125 C210,125 212,78 218,78 C224,78 226,125 234,125Z"/>
      <path class="r" d="M226,125 C236,125 232,62 240,62 C248,62 244,125 254,125Z"/>
    </g>
    <line x1="38" y1="68" x2="38" y2="125" stroke="#7a99c7" stroke-width=".6"/>
    <circle class="r" cx="38" cy="66" r="6"/><text class="on-dark" x="34.5" y="67.2">30K</text>
    <circle class="r" cx="240" cy="52" r="6"/><text class="on-dark" x="236.5" y="53.2">90K</text>
    <g class="label"><text x="34" y="133">2013</text><text x="56" y="133">2014</text><text x="78" y="133">2015</text><text x="100" y="133">2016</text><text x="122" y="133">2017</text><text x="144" y="133">2018</text><text x="166" y="133">2019</text><text x="188" y="133">2020</text><text x="210" y="133">2021</text><text x="232" y="133">2022</text></g>
  </svg>
  <h2 class="slide-title">MOUNTAIN DATA STYLE - 1</h2><p class="slide-sub">Enter your subtitle here</p>
  <div class="brand-mark">VELA CREST</div><div class="slide-footer">WWW.VELACREST.EXAMPLE</div>
</section>

<section class="slide" style="left:803px;top:93px">
  <svg class="content" viewBox="0 0 281 158">
    <text class="copy" x="18" y="32">Vela Crest turns complex data into simple insight for faster and smarter decisions every day,</text>
    <text class="copy" x="18" y="37">helping leaders grow revenue, reduce risk and see the whole business clearly.</text>
    <path class="r" d="M18,128 C32,128 36,92 50,92 C64,92 62,128 76,128Z"/>
    <path class="k" d="M52,128 C64,128 64,66 82,66 C100,66 98,128 110,128Z"/>
    <path class="r" d="M88,128 C100,128 100,76 118,76 C136,76 134,128 146,128Z"/>
    <path class="k" d="M124,128 C136,128 136,70 154,70 C172,70 170,128 182,128Z"/>
    <path class="r" d="M160,128 C172,128 172,66 190,66 C208,66 206,128 218,128Z"/>
    <path class="k" d="M196,128 C208,128 210,86 226,86 C242,86 246,128 264,128Z"/>
    <g class="label"><text x="42" y="80">5,900</text><text x="76" y="60">9,000</text><text x="112" y="70">6,500</text><text x="148" y="64">6,800</text><text x="184" y="60">7,600</text><text x="220" y="80">6,000</text></g>
    <g class="label"><text x="42" y="140">TITLE - 01</text><text x="77" y="140">TITLE - 02</text><text x="113" y="140">TITLE - 03</text><text x="149" y="140">TITLE - 04</text><text x="185" y="140">TITLE - 05</text><text x="221" y="140">TITLE - 06</text></g>
  </svg>
  <h2 class="slide-title">MOUNTAIN DATA STYLE - 2</h2><p class="slide-sub">Enter your subtitle here</p>
  <div class="brand-mark">VELA CREST</div><div class="slide-footer">WWW.VELACREST.EXAMPLE</div>
</section>

<!-- Row 2 -->
<section class="slide" style="left:147px;top:274px">
  <svg class="content" viewBox="0 0 281 158">
    <text class="copy" x="18" y="48">Simple insight drawn from complex data</text>
    <text class="copy" x="18" y="53">sets, built so leaders can act quickly</text>
    <text class="copy" x="18" y="58">and measure results across every unit.</text>
    <circle class="k" cx="32" cy="95" r="8"/><circle class="r" cx="61" cy="95" r="8"/><circle class="k" cx="90" cy="95" r="8"/>
    <rect x="29" y="92" width="6" height="6" rx="1" fill="none" stroke="#fff" stroke-width=".8"/>
    <circle cx="61" cy="95" r="3" fill="none" stroke="#fff" stroke-width=".8"/>
    <polygon points="86,95 90,92 94,95 90,98" fill="none" stroke="#fff" stroke-width=".8"/>
    <g class="label"><text x="28" y="114">95%</text><text x="57" y="114">35%</text><text x="86" y="114">15%</text></g>
    <g class="copy"><text x="20" y="119">Performance</text><text x="50" y="119">Performance</text><text x="79" y="119">Performance</text></g>
    <g stroke="#e3e3e3" stroke-width=".4"><line x1="140" y1="55" x2="260" y2="55"/><line x1="140" y1="68" x2="260" y2="68"/><line x1="140" y1="81" x2="260" y2="81"/><line x1="140" y1="94" x2="260" y2="94"/><line x1="140" y1="107" x2="260" y2="107"/><line x1="140" y1="120" x2="260" y2="120"/></g>
    <polyline fill="none" stroke="#999" stroke-width=".6" points="145,100 153,78 161,96 169,70 177,92 185,84 193,98 201,66 209,90 217,80 225,102 233,86 241,94 249,88"/>
    <polyline fill="none" stroke="#6aa832" stroke-width=".6" stroke-dasharray="1 1" points="145,90 153,96 161,84 169,104 177,88 185,98 193,80 201,94 209,86 217,100 225,82 233,98 241,84 249,92"/>
    <rect class="k" x="190" y="45" width="3" height="3"/><text class="copy" x="195" y="48">Page Views</text>
    <rect x="214" y="45" width="3" height="3" fill="#6aa832"/><text class="copy" x="219" y="48">Visitors</text>
    <text class="copy" x="143" y="130">FL  PH  ML  SJ  DK  HG  SO  UD  SM  MN  UK  US  IN  KR</text>
  </svg>
  <h2 class="slide-title">INFOGRAPHIC DATA DISPLAY</h2><p class="slide-sub">Enter your subtitle here</p>
  <div class="brand-mark">VELA CREST</div><div class="slide-footer">WWW.VELACREST.EXAMPLE</div>
</section>

<section class="slide" style="left:475px;top:274px">
  <svg class="content" viewBox="0 0 281 158">
    <text class="copy" x="18" y="32">Vela Crest turns complex data into simple insight for faster and smarter decisions every day,</text>
    <text class="copy" x="18" y="37">helping leaders grow revenue, reduce risk and see the whole business clearly.</text>
    <g class="label"><text x="28" y="56">100%</text><text x="30" y="71">75%</text><text x="30" y="86">50%</text><text x="30" y="101">25%</text><text x="32" y="116">0%</text></g>
    <g class="g"><rect x="52" y="54" width="11" height="62"/><rect x="75" y="54" width="11" height="62"/><rect x="98" y="54" width="11" height="62"/><rect x="121" y="54" width="11" height="62"/><rect x="144" y="54" width="11" height="62"/><rect x="167" y="54" width="11" height="62"/><rect x="190" y="54" width="11" height="62"/><rect x="213" y="54" width="11" height="62"/><rect x="236" y="54" width="11" height="62"/></g>
    <rect class="r" x="54" y="72" width="7" height="44"/><rect class="k" x="77" y="59" width="7" height="57"/><rect class="r" x="100" y="77" width="7" height="39"/><rect class="k" x="123" y="59" width="7" height="57"/><rect class="r" x="146" y="85" width="7" height="31"/><rect class="k" x="169" y="78" width="7" height="38"/><rect class="r" x="192" y="59" width="7" height="57"/><rect class="k" x="215" y="78" width="7" height="38"/><rect class="r" x="238" y="59" width="7" height="57"/>
    <g class="on-dark" style="font-size:2.6px"><text x="54.5" y="114">70%</text><text x="77.5" y="114">89%</text><text x="100.5" y="114">62%</text><text x="123.5" y="114">98%</text><text x="146.5" y="114">50%</text><text x="169.5" y="114">60%</text><text x="192.5" y="114">94%</text><text x="215.5" y="114">61%</text><text x="238.5" y="114">90%</text></g>
    <g class="label"><text x="53" y="126">2001</text><text x="76" y="126">2002</text><text x="99" y="126">2003</text><text x="122" y="126">2004</text><text x="145" y="126">2005</text><text x="168" y="126">2006</text><text x="191" y="126">2007</text><text x="214" y="126">2008</text><text x="237" y="126">2009</text></g>
  </svg>
  <h2 class="slide-title">INFOGRAPHIC DATA DISPLAY</h2><p class="slide-sub">Enter your subtitle here</p>
  <div class="brand-mark">VELA CREST</div><div class="slide-footer">WWW.VELACREST.EXAMPLE</div>
</section>

<section class="slide" style="left:803px;top:274px">
  <svg class="content" viewBox="0 0 281 158">
    <text class="copy" x="18" y="32">Vela Crest turns complex data into simple insight for faster and smarter decisions every day,</text>
    <text class="copy" x="18" y="37">helping leaders grow revenue, reduce risk and see the whole business clearly.</text>
    <circle cx="131" cy="88" r="34" fill="none" stroke="#ececec" stroke-width="6"/>
    <circle cx="131" cy="88" r="27" fill="none" stroke="#ececec" stroke-width="5"/>
    <path d="M131,54 A34,34 0 0 1 163,100" fill="none" stroke="var(--red)" stroke-width="6"/>
    <path d="M131,61 A27,27 0 1 1 110,105" fill="none" stroke="var(--black)" stroke-width="5"/>
    <circle cx="131" cy="88" r="20" fill="none" stroke="var(--red)" stroke-width="1.5"/>
    <circle cx="131" cy="88" r="18" fill="#fff"/>
    <text class="label-b" x="119" y="87">Your Title Here</text>
    <text class="copy" x="121" y="92">Add a short line</text>
    <text class="label-b" x="18" y="74">Your Title Here</text><text class="copy" x="18" y="79">Add a short note about this item</text>
    <text class="label-b" x="18" y="100" style="fill:var(--red)">Your Title Here</text><text class="copy" x="18" y="105">Add a short note about this item</text>
    <text class="label-b" x="202" y="80" style="fill:var(--red)">Your Title Here</text><text class="copy" x="202" y="85">Add a short note about this item</text>
    <text class="label-b" x="202" y="110">Your Title Here</text><text class="copy" x="202" y="115">Add a short note about this item</text>
  </svg>
  <h2 class="slide-title">INFOGRAPHIC DATA DISPLAY</h2><p class="slide-sub">Enter your subtitle here</p>
  <div class="brand-mark">VELA CREST</div><div class="slide-footer">WWW.VELACREST.EXAMPLE</div>
</section>

<!-- Row 3 -->
<section class="slide" style="left:147px;top:462px">
  <svg class="content" viewBox="0 0 281 158">
    <text class="copy" x="18" y="32">Vela Crest turns complex data into simple insight for faster and smarter decisions every day,</text>
    <text class="copy" x="18" y="37">helping leaders grow revenue, reduce risk and see the whole business clearly.</text>
    <use href="#hex" class="k" x="117" y="66"/><use href="#hex" class="r" x="149" y="66"/>
    <use href="#hex" class="r" x="133" y="94"/><use href="#hex" class="k" x="165" y="94"/>
    <use href="#hex" class="k" x="117" y="122"/><use href="#hex" class="r" x="149" y="122"/>
    <g class="big" style="font-size:5px"><text x="111" y="68">60%</text><text x="143" y="68">35%</text><text x="127" y="96">50%</text><text x="159" y="96">60%</text><text x="113" y="124">80</text><text x="143" y="124">35%</text></g>
    <g class="label"><text x="62" y="64">Title - 01</text><text x="78" y="93">Title - 01</text><text x="64" y="122">Title - 01</text><text x="178" y="64">Title - 01</text><text x="195" y="93">Title - 01</text><text x="186" y="122">Title - 01</text></g>
    <g class="copy"><text x="32" y="70">Short note on this data item</text><text x="46" y="99">Short note on this data item</text><text x="32" y="128">Short note on this data item</text><text x="186" y="70">Short note on this data item</text><text x="186" y="99">Short note on this data item</text><text x="186" y="128">Short note on this data item</text></g>
  </svg>
  <h2 class="slide-title">INFOGRAPHIC DATA DISPLAY</h2><p class="slide-sub">Enter your subtitle here</p>
  <div class="brand-mark">VELA CREST</div><div class="slide-footer">WWW.VELACREST.EXAMPLE</div>
</section>

<section class="slide" style="left:475px;top:462px">
  <svg class="content" viewBox="0 0 281 158">
    <text class="copy" x="10" y="38">Vela Crest turns complex data into simple</text>
    <text class="copy" x="10" y="44">insight so leaders can act with speed and</text>
    <text class="copy" x="10" y="50">confidence, growing revenue while they</text>
    <text class="copy" x="10" y="56">reduce risk across every business unit.</text>
    <rect class="r" x="24" y="109" width="40" height="36"/><text class="on-dark" x="34" y="115">Text - 01</text>
    <rect class="k" x="62" y="92" width="40" height="36"/><text class="on-dark" x="72" y="98">Text - 02</text>
    <rect class="r" x="100" y="76" width="40" height="36"/><text class="on-dark" x="110" y="82">Text - 03</text>
    <rect class="k" x="148" y="58" width="40" height="36"/><text class="on-dark" x="158" y="64">Text - 04</text>
    <polygon class="r" points="192,40 236,40 236,33 264,58 236,83 236,76 192,76"/><text class="on-dark" x="215" y="50">Text - 05</text>
    <g class="on-dark" style="font-size:2.6px;font-weight:400"><text x="28" y="122">Step one detail</text><text x="66" y="105">Step two detail</text><text x="104" y="89">Step three detail</text><text x="152" y="71">Step four detail</text><text x="210" y="58">Step five detail</text></g>
    <text class="copy" x="176" y="118">Each step moves raw data closer</text>
    <text class="copy" x="176" y="124">to a clear and simple decision for</text>
    <text class="copy" x="176" y="130">the teams who rely on it daily.</text>
  </svg>
  <h2 class="slide-title">DATA DISPLAY STEP WISE</h2><p class="slide-sub">Enter your subtitle here</p>
  <div class="brand-mark">VELA CREST</div><div class="slide-footer">WWW.VELACREST.EXAMPLE</div>
</section>

<section class="slide" style="left:803px;top:462px">
  <svg class="content" viewBox="0 0 281 158">
    <text class="copy" x="18" y="32">Vela Crest turns complex data into simple insight for faster and smarter decisions every day,</text>
    <text class="copy" x="18" y="37">helping leaders grow revenue, reduce risk and see the whole business clearly for all teams.</text>
    <rect class="r" x="34" y="60" width="60" height="7"/><rect class="k" x="95" y="60" width="38" height="7"/><rect class="r" x="134" y="60" width="38" height="7"/><rect class="k" x="173" y="60" width="38" height="7"/><rect class="r" x="212" y="60" width="38" height="7"/>
    <g class="on-dark"><text x="56" y="65">Your Text</text><text x="107" y="65">Text-01</text><text x="146" y="65">Text-02</text><text x="185" y="65">Text-03</text><text x="224" y="65">Text-04</text></g>
    <g stroke="var(--rule)" stroke-width=".4"><line x1="34" y1="78" x2="250" y2="78"/><line x1="34" y1="89" x2="250" y2="89"/><line x1="34" y1="100" x2="250" y2="100"/><line x1="34" y1="111" x2="250" y2="111"/><line x1="34" y1="122" x2="250" y2="122"/></g>
    <g class="copy" style="fill:var(--red)"><text x="36" y="75">Short row label text</text><text x="36" y="86">Short row label text</text><text x="36" y="97">Short row label text</text><text x="36" y="108">Short row label text</text><text x="36" y="119">Short row label text</text></g>
    <g fill="none" stroke-width=".8">
      <g stroke="#222"><path d="M111,73 l2,2 l4,-4"/><path d="M111,84 l2,2 l4,-4"/><path d="M189,73 l2,2 l4,-4"/><path d="M189,84 l2,2 l4,-4"/><path d="M189,95 l2,2 l4,-4"/><path d="M189,106 l2,2 l4,-4"/></g>
      <g stroke="#c9a800"><path d="M150,73 l2,2 l4,-4"/><path d="M150,84 l2,2 l4,-4"/><path d="M150,95 l2,2 l4,-4"/><path d="M228,73 l2,2 l4,-4"/><path d="M228,84 l2,2 l4,-4"/><path d="M228,95 l2,2 l4,-4"/><path d="M228,106 l2,2 l4,-4"/><path d="M228,117 l2,2 l4,-4"/></g>
    </g>
    <rect class="r" x="34" y="128" width="60" height="8"/><rect class="k" x="95" y="128" width="38" height="8"/><rect class="r" x="134" y="128" width="38" height="8"/><rect class="k" x="173" y="128" width="38" height="8"/><rect class="r" x="212" y="128" width="38" height="8"/>
    <g class="on-dark"><text x="58" y="133">Price</text><text x="107" y="133">32.00$</text><text x="146" y="133">48.00$</text><text x="185" y="133">62.00$</text><text x="224" y="133">78.00$</text></g>
  </svg>
  <h2 class="slide-title">TABLE DATA</h2><p class="slide-sub">Enter your subtitle here</p>
  <div class="brand-mark">VELA CREST</div><div class="slide-footer">WWW.VELACREST.EXAMPLE</div>
</section>

<!-- Row 4 -->
<section class="slide" style="left:147px;top:659px">
  <svg class="content" viewBox="0 0 281 158">
    <g class="copy"><text x="14" y="34">Vela Crest turns complex data</text><text x="14" y="40">into simple insight so every</text><text x="14" y="46">leader can act with speed and</text><text x="14" y="52">confidence across the firm.</text><text x="14" y="68">Clear dashboards show what</text><text x="14" y="74">matters most, helping teams</text><text x="14" y="80">grow revenue and reduce risk</text><text x="14" y="86">while keeping every report</text><text x="14" y="92">simple, current and useful</text><text x="14" y="98">for people at every level.</text></g>
    <polygon class="k" points="262,16 281,16 281,150 262,150"/>
    <polygon class="r" points="262,20 281,14 281,40 262,40"/><polygon class="r" points="262,60 281,60 281,80 262,80"/><polygon class="r" points="262,100 281,100 281,120 262,120"/><polygon class="r" points="262,130 281,130 281,148 262,148"/>
    <polygon class="r" points="140,28 262,28 262,46 140,46 133,37"/>
    <polygon class="k" points="118,50 262,50 262,68 118,68 111,59"/>
    <polygon class="r" points="140,72 262,72 262,90 140,90 133,81"/>
    <polygon class="k" points="118,94 262,94 262,112 118,112 111,103"/>
    <polygon class="r" points="140,116 262,116 262,134 140,134 133,125"/>
    <g class="big" style="font-size:7px;font-weight:400"><text x="142" y="40">40%</text><text x="120" y="62">65%</text><text x="142" y="84">90%</text><text x="120" y="106">90%</text><text x="142" y="128">75%</text></g>
    <g class="on-dark" style="font-weight:400"><text x="229" y="35">Creative</text><text x="229" y="57">Creative</text><text x="229" y="79">Creative</text><text x="229" y="101">Creative</text><text x="229" y="123">Creative</text></g>
    <g class="on-dark" style="font-weight:400;font-size:2.6px"><text x="216" y="40">Short line of detail</text><text x="216" y="62">Short line of detail</text><text x="216" y="84">Short line of detail</text><text x="216" y="106">Short line of detail</text><text x="216" y="128">Short line of detail</text></g>
    <g fill="none" stroke="#fff" stroke-width=".7"><path d="M252,37 l1.5,1.5 l3,-3"/><circle cx="254" cy="59" r="2.2"/><rect x="252" y="79" width="4" height="4"/><path d="M252,101 l4,4 M256,101 l-4,4"/><path d="M251,126 q3,-5 6,0z"/></g>
  </svg>
  <h2 class="slide-title">DATA DISPLAY WALL STYLE</h2><p class="slide-sub">Enter your subtitle here</p>
  <div class="brand-mark">VELA CREST</div><div class="slide-footer">WWW.VELACREST.EXAMPLE</div>
</section>

<section class="slide" style="left:475px;top:659px">
  <svg class="content" viewBox="0 0 281 158">
    <text class="copy" x="18" y="32">Vela Crest turns complex data into simple insight for faster and smarter decisions every day,</text>
    <text class="copy" x="18" y="37">helping leaders grow revenue, reduce risk and see the whole business clearly.</text>
    <rect x="22" y="58" width="120" height="82" fill="#8c9494" opacity=".75" role="img" aria-label="World map with red and black location markers"/>
    <g><rect class="r" x="152" y="86" width="6" height="34" rx="3"/><rect class="r" x="164" y="96" width="6" height="24" rx="3"/><rect class="r" x="176" y="84" width="6" height="36" rx="3"/><rect class="k" x="188" y="64" width="6" height="56" rx="3"/><rect fill="#c8c8c8" x="200" y="100" width="6" height="20" rx="3"/><rect fill="#c8c8c8" x="212" y="94" width="6" height="26" rx="3"/><rect fill="#c8c8c8" x="224" y="100" width="6" height="20" rx="3"/><rect class="k" x="236" y="82" width="6" height="38" rx="3"/><rect fill="#c8c8c8" x="248" y="78" width="6" height="42" rx="3"/></g>
    <text class="copy" x="186" y="61">38%</text><text class="copy" x="234" y="79">65%</text>
    <text class="copy" x="152" y="128">US   RL   BR   AU   RN   CD   AU   MN   LT</text>
  </svg>
  <h2 class="slide-title">WORLD MAP DATA DISPLAY</h2><p class="slide-sub">Enter your subtitle here</p>
  <div class="brand-mark">VELA CREST</div><div class="slide-footer">WWW.VELACREST.EXAMPLE</div>
</section>

<section class="slide" style="left:803px;top:659px">
  <svg class="content" viewBox="0 0 281 158">
    <text class="copy" x="18" y="32">Vela Crest turns complex data into simple insight for faster and smarter decisions every day,</text>
    <text class="copy" x="18" y="37">helping leaders grow revenue, reduce risk and see the whole business clearly.</text>
    <rect class="photo-b" x="44" y="52" width="196" height="86" rx="3" role="img" aria-label="Laptops, tablet and phone showing data dashboards"/>
  </svg>
  <h2 class="slide-title">SYSTEM DATA DISPLAY</h2><p class="slide-sub">Enter your subtitle here</p>
  <div class="brand-mark">VELA CREST</div><div class="slide-footer">WWW.VELACREST.EXAMPLE</div>
</section>

<!-- Row 5 -->
<section class="slide" style="left:147px;top:838px">
  <svg class="content" viewBox="0 0 281 158">
    <text class="copy" x="18" y="32">Vela Crest turns complex data into simple insight for faster and smarter decisions every day,</text>
    <text class="copy" x="18" y="37">helping leaders grow revenue, reduce risk and see the whole business clearly.</text>
    <rect class="photo-b" x="190" y="44" width="91" height="106" role="img" aria-label="Laptop on a desk showing charts"/>
    <circle class="r" cx="26" cy="70" r="6"/><circle class="r" cx="108" cy="70" r="6"/><circle class="r" cx="26" cy="106" r="6"/><circle class="r" cx="108" cy="106" r="6"/>
    <g fill="none" stroke="#fff" stroke-width=".8"><path d="M23,68 a3,3 0 1 0 6,0"/><path d="M105,71 l2,2 l4,-4"/><path d="M23,109 v-3 M26,109 v-5 M29,109 v-2"/><circle cx="107" cy="105" r="2"/></g>
    <g class="label-b" style="font-size:3.6px"><text x="38" y="69">Title Goes Here</text><text x="120" y="69">Title Goes Here</text><text x="38" y="105">Title Goes Here</text><text x="120" y="105">Title Goes Here</text></g>
    <g class="copy"><text x="38" y="75">Suited for all business decks</text><text x="120" y="75">Suited for all business decks</text><text x="38" y="111">Suited for all business decks</text><text x="120" y="111">Suited for all business decks</text></g>
  </svg>
  <h2 class="slide-title">SYSTEM DATA DISPLAY 2</h2><p class="slide-sub">Enter your subtitle here</p>
  <div class="brand-mark">VELA CREST</div><div class="slide-footer">WWW.VELACREST.EXAMPLE</div>
</section>

<section class="slide" style="left:475px;top:838px">
  <svg class="content" viewBox="0 0 281 158">
    <rect x="0" y="0" width="112" height="94" fill="#3b3d40" role="img" aria-label="Team working at a desk, dark toned"/>
    <g style="font:italic 4px 'Open Sans',sans-serif;fill:#fff"><text x="24" y="26">Simple insight is the clearest</text><text x="22" y="32">path from raw data to a smart</text><text x="22" y="38">decision. Vela Crest helps every</text><text x="22" y="44">leader see the whole business</text><text x="22" y="50">and act on it with confidence,</text><text x="22" y="56">growing revenue while</text><text x="22" y="62">reducing risk.</text></g>
    <g class="copy"><text x="120" y="34">Vela Crest turns complex data into simple insight for</text><text x="120" y="39">faster decisions across every part of the business.</text><text x="120" y="50">Clear dashboards show what matters most, helping</text><text x="120" y="55">teams grow revenue, reduce risk and stay focused</text><text x="120" y="60">on the numbers that truly move the company.</text></g>
    <polygon class="r" points="16,108 60,108 64,112 60,116 16,116"/><polygon class="k" points="60,108 104,108 108,112 104,116 60,116 64,112"/><polygon class="r" points="104,108 148,108 152,112 148,116 104,116 108,112"/><polygon class="k" points="148,108 192,108 196,112 192,116 148,116 152,112"/>
    <g class="on-dark" style="font-weight:400"><text x="36" y="113">2010</text><text x="80" y="113">2012</text><text x="124" y="113">2015</text><text x="168" y="113">2017</text></g>
    <text x="207" y="114" style="font:400 6px 'Michroma',sans-serif;fill:var(--black)">VELA CREST</text>
    <g class="label-b" style="font-size:3.4px"><text x="25" y="128">Title Goes Here</text><text x="69" y="128">Title Goes Here</text><text x="113" y="128">Title Goes Here</text><text x="157" y="128">Title Goes Here</text></g>
    <g class="copy"><text x="24" y="134">For any business deck</text><text x="68" y="134">For any business deck</text><text x="112" y="134">For any business deck</text><text x="156" y="134">For any business deck</text></g>
  </svg>
  <h2 class="slide-title" style="left:116px">YOUR TITLE HERE</h2><p class="slide-sub" style="left:116px">Enter your subtitle here</p>
  <div class="brand-mark">VELA CREST</div><div class="slide-footer">WWW.VELACREST.EXAMPLE</div>
</section>

<section class="slide" style="left:803px;top:838px">
  <svg class="content" viewBox="0 0 281 158">
    <rect class="photo-a" x="0" y="0" width="102" height="52" role="img" aria-label="Colleagues meeting around a table"/>
    <rect class="photo-b" x="0" y="52" width="102" height="50" role="img" aria-label="Hands working on a laptop"/>
    <rect class="photo-b" x="0" y="102" width="102" height="50" role="img" aria-label="Hand writing notes beside a laptop"/>
    <rect x="102" y="0" width="74" height="152" fill="#55595e" role="img" aria-label="Person holding a tablet"/>
    <circle class="r" cx="198" cy="46" r="5"/><circle class="r" cx="198" cy="80" r="5"/><circle class="r" cx="198" cy="113" r="5"/>
    <g class="on-dark" style="font-size:3px"><text x="196" y="47">01</text><text x="196" y="81">02</text><text x="196" y="114">03</text></g>
    <g class="label-b" style="font-size:3.6px"><text x="210" y="39">Title Goes Here</text><text x="210" y="73">Title Goes Here</text><text x="210" y="106">Title Goes Here</text></g>
    <g class="copy"><text x="210" y="45">Suited for all business decks</text><text x="210" y="79">Suited for all business decks</text><text x="210" y="112">Suited for all business decks</text></g>
  </svg>
  <div class="brand-mark">VELA CREST</div><div class="slide-footer">WWW.VELACREST.EXAMPLE</div>
</section>

<!-- Row 6 -->
<section class="slide" style="left:147px;top:1024px">
  <svg class="content" viewBox="0 0 281 158">
    <rect class="photo-a" x="29" y="35" width="71" height="44" role="img" aria-label="Person writing at a desk"/>
    <rect class="photo-b" x="105" y="35" width="71" height="44" role="img" aria-label="Hands on a tablet"/>
    <rect class="photo-a" x="181" y="35" width="71" height="44" role="img" aria-label="Business person at a laptop"/>
    <rect class="photo-b" x="29" y="86" width="71" height="44" role="img" aria-label="Team in a meeting"/>
    <rect class="photo-a" x="105" y="86" width="71" height="44" role="img" aria-label="Hand writing in a notebook"/>
    <rect class="photo-a" x="181" y="86" width="71" height="44" role="img" aria-label="Open book on a table"/>
    <g class="k" opacity=".75"><rect x="29" y="73" width="71" height="6"/><rect x="105" y="73" width="71" height="6"/><rect x="181" y="73" width="71" height="6"/><rect x="29" y="124" width="71" height="6"/><rect x="105" y="124" width="71" height="6"/><rect x="181" y="124" width="71" height="6"/></g>
    <g class="on-dark" style="font-size:3px"><text x="53" y="77">Enter Your Title</text><text x="129" y="77">Enter Your Title</text><text x="205" y="77">Enter Your Title</text><text x="53" y="128">Enter Your Title</text><text x="129" y="128">Enter Your Title</text><text x="205" y="128">Enter Your Title</text></g>
  </svg>
  <h2 class="slide-title">PORTFOLIO DESIGN IDEA - 1</h2><p class="slide-sub">Enter your subtitle here</p>
  <div class="brand-mark">VELA CREST</div><div class="slide-footer">WWW.VELACREST.EXAMPLE</div>
</section>

<section class="slide" style="left:475px;top:1024px">
  <svg class="content" viewBox="0 0 281 158">
    <rect class="photo-b" x="21" y="35" width="51" height="76" role="img" aria-label="Notes on a chart-covered wall"/>
    <rect class="photo-b" x="83" y="35" width="51" height="76" role="img" aria-label="Person working in an office"/>
    <rect class="photo-a" x="145" y="35" width="51" height="76" role="img" aria-label="Hand writing on paper"/>
    <rect x="207" y="35" width="51" height="76" fill="#2f3133" role="img" aria-label="Light bulb on a dark background"/>
    <rect class="k" x="21" y="111" width="51" height="7"/><rect class="r" x="83" y="111" width="51" height="7"/><rect class="k" x="145" y="111" width="51" height="7"/><rect class="r" x="207" y="111" width="51" height="7"/>
    <g class="on-dark" style="font-size:3px"><text x="34" y="116">Enter Your Title</text><text x="96" y="116">Enter Your Title</text><text x="158" y="116">Enter Your Title</text><text x="220" y="116">Enter Your Title</text></g>
    <g class="copy"><text x="24" y="126">Suited for all business</text><text x="86" y="126">Suited for all business</text><text x="148" y="126">Suited for all business</text><text x="210" y="126">Suited for all business</text><text x="26" y="131">and personal decks</text><text x="88" y="131">and personal decks</text><text x="150" y="131">and personal decks</text><text x="212" y="131">and personal decks</text></g>
  </svg>
  <h2 class="slide-title">PORTFOLIO DESIGN IDEA - 2</h2><p class="slide-sub">Enter your subtitle here</p>
  <div class="brand-mark">VELA CREST</div><div class="slide-footer">WWW.VELACREST.EXAMPLE</div>
</section>

<section class="slide" style="left:803px;top:1024px">
  <svg class="content" viewBox="0 0 281 158">
    <text class="copy" x="18" y="32">Vela Crest turns complex data into simple insight for faster and smarter decisions every day,</text>
    <text class="copy" x="18" y="37">helping leaders grow revenue, reduce risk and see the whole business clearly.</text>
    <rect class="photo-a" x="0" y="52" width="100" height="50" role="img" aria-label="Person working at a laptop"/>
    <rect class="photo-a" x="0" y="104" width="100" height="48" role="img" aria-label="Books on a shelf and an open book"/>
    <rect class="photo-b" x="140" y="60" width="40" height="40" role="img" aria-label="Analyst reviewing charts"/>
    <rect class="k" x="180" y="60" width="42" height="40"/>
    <rect class="k" x="150" y="100" width="42" height="40"/>
    <rect class="photo-b" x="192" y="100" width="30" height="40" role="img" aria-label="Charts on a screen"/>
    <g class="on-dark"><text x="188" y="70">Your Title Here</text><text x="158" y="110">Your Title Here</text></g>
    <g class="on-dark" style="font-size:2.6px;font-weight:400"><text x="186" y="78">Short line of detail</text><text x="186" y="83">for this item here</text><text x="156" y="118">Short line of detail</text><text x="156" y="123">for this item here</text></g>
  </svg>
  <h2 class="slide-title">YOUR TITLE HERE</h2><p class="slide-sub">Enter your subtitle here</p>
  <div class="brand-mark">VELA CREST</div><div class="slide-footer">WWW.VELACREST.EXAMPLE</div>
</section>
</body>
</html>
```